RTavenor Business Cards & Letterhead

I have a logo but need a design for some new business cards. We are a Design-Build Firm that specializes in the design and construction of commercial projects.
the cards need to be professional. no cartoon stuff.
i would like to have the cards in AI format so I can update the card as needed. Logo is provided.
Our Address is: 4187 Marlowe Ct. Harlow Springs, New Carrick 27614

```html
<!DOCTYPE html>
<html lang="en">
<head>
<meta charset="utf-8">
<title>RTavenor Business Card</title>
<link href="https://fonts.googleapis.com/css2?family=Montserrat:wght@400;500;700;800&display=swap" rel="stylesheet">
<style>
  :root{
    --page:#d9d9d9;
    --blue-light:#6aa4c9;
    --blue-mid:#2f86bb;
    --blue-dark:#125f97;
    --blue-ink:#2f72a3;
    --emboss:#5d9dc8;
    --card-white:#f3f3f3;
    --card-white-2:#e6e6e6;
    --ink:#4a4a4a;
    --ink-soft:#5e5e5e;
    --rule:#3e3e3e;
  }
  *{box-sizing:border-box;margin:0;padding:0}
  html,body{width:1200px;height:1200px;overflow:hidden;background:var(--page)}
  body{font-family:"Montserrat",Arial,sans-serif;position:relative}
  .card{position:absolute;left:180px;width:840px;height:480px;border-radius:26px;overflow:hidden}
  .card--back{top:90px;background:linear-gradient(110deg,var(--blue-light) 0%,var(--blue-mid) 45%,var(--blue-dark) 100%)}
  .card--front{top:630px;background:linear-gradient(110deg,var(--card-white) 0%,var(--card-white-2) 100%)}
  .back-wordmark{position:absolute;left:0;right:0;top:200px;text-align:center;font-weight:800;font-size:70px;letter-spacing:2px;color:var(--emboss)}
  .back-wordmark sup{font-size:18px;font-weight:500;vertical-align:top;position:relative;top:6px}
  .holder{position:absolute;left:80px;top:70px}
  .holder-name{font-weight:800;font-size:36px;color:var(--blue-ink);letter-spacing:.5px}
  .holder-title{font-weight:400;font-size:20px;color:var(--ink-soft);margin:6px 0 0 14px}
  .divider{position:absolute;left:94px;right:60px;top:168px;height:2px;background:var(--rule)}
  .contact{position:absolute;left:112px;top:232px;color:var(--ink-soft);font-size:20px;line-height:30px}
  .contact-address{margin-bottom:8px}
  .contact-row{display:flex;align-items:center;gap:14px}
  .contact-row svg{width:18px;height:18px;flex:none;fill:var(--blue-ink)}
  .front-wordmark{position:absolute;right:58px;bottom:92px;display:flex;align-items:center;gap:10px;font-weight:800;font-size:38px;color:var(--ink);letter-spacing:1px}
  .front-wordmark .mark-square{width:26px;height:26px;background:var(--blue-ink)}
  .front-wordmark .reg{font-size:12px;font-weight:500;align-self:flex-start;margin-left:-6px;margin-top:2px}
</style>
</head>
<body>
  <section class="card card--back">
    <div class="back-wordmark">RTAVENOR<sup>®</sup></div>
  </section>

  <section class="card card--front">
    <div class="holder">
      <div class="holder-name">Warren Tavenor</div>
      <div class="holder-title">President</div>
    </div>
    <div class="divider"></div>

    <div class="contact">
      <div class="contact-address">4187 Marlowe Ct. Harlow Springs,<br>New Carrick 27614</div>
      <div class="contact-row">
        <svg viewBox="0 0 24 24" aria-hidden="true"><path d="M6.6 10.8a15.2 15.2 0 0 0 6.6 6.6l2.2-2.2c.3-.3.7-.4 1-.2 1.1.4 2.3.6 3.6.6.6 0 1 .4 1 1V20c0 .6-.4 1-1 1A17 17 0 0 1 3 4c0-.6.4-1 1-1h3.5c.6 0 1 .4 1 1 0 1.3.2 2.5.6 3.6.1.3 0 .7-.2 1z"/></svg>
        <span>(555)-214-0376</span>
      </div>
      <div class="contact-row">
        <svg viewBox="0 0 24 24" aria-hidden="true"><path d="M2 5h20v14H2zM3.5 6.5 12 13l8.5-6.5z" fill-rule="evenodd"/></svg>
        <span>info@rtavenor.com</span>
      </div>
      <div class="contact-row">
        <svg viewBox="0 0 24 24" aria-hidden="true"><path d="M12 2a10 10 0 1 0 0 20 10 10 0 0 0 0-20zm-1 2.1C9.6 5.6 8.7 8 8.6 11H4.1A8 8 0 0 1 11 4.1zm2 0A8 8 0 0 1 19.9 11h-4.5c-.1-3-1-5.4-2.4-6.9zM10.6 11c.1-2.6.7-4.6 1.4-5.6.7 1 1.3 3 1.4 5.6zm-6.5 2h4.5c.1 3 1 5.4 2.4 6.9A8 8 0 0 1 4.1 13zm6.5 0h2.8c-.1 2.6-.7 4.6-1.4 5.6-.7-1-1.3-3-1.4-5.6zm4.8 0h4.5a8 8 0 0 1-6.9 6.9c1.4-1.5 2.3-3.9 2.4-6.9z"/></svg>
        <span>www.rtavenor.com</span>
      </div>
    </div>

    <div class="front-wordmark"><span class="mark-square"></span>RTAVENOR<span class="reg">®</span></div>
  </section>
</body>
</html>
```